Company or website name
- dalewintham.com
- Links to the website
- Vita Forge
- Describe your company and organization and target audience
- Founded by celebrity personal trainer and media personality Dale Wintham, Vita Forge provides high quality on-site fitness and wellness classes, and personal trainers for businesses and residential gyms throughout New York City. Our target audience are residents of high end buildings in NYC, that expect excellence and luxury
- The design should have the following
- This is a 24"x36" Poster for a complimentary event at a high end building. I would like the poster to look high end, luxury and simple and chique. The words should be clear and easy to read. It would be great to have a final copy that we can send to the printer and one which we can edit for future events Here is the text: The Halcott Spires Gym Complimentary Fitness & Wellness Event Complimentary Yoga, Pilates & Interval Training Bootcamp Classes PLUS: 30 Minute Private Training Sessions *Kids Karate Classes Also Available Saturday May 18th, 25th & June 1st Time: 9:00am - 12:15pm Halcott Spires Gym Schedule: 9:00am - 9:30am Yoga 9:45am - 10:15am Interval Training Bootcamp 11:45am -12:15pm Pilates 9:00am - 12:00pm Private Training Sessions Special Introductory Rate on Future Packages During Promotion www.Vitaforge.tv Info@vitaforge.tv
- Other Facts

```html
<!DOCTYPE html>
<html lang="en">
<head>
<meta charset="utf-8">
<title>Vita Forge – Complimentary Fitness &amp; Wellness Poster</title>
<link href="https://fonts.googleapis.com/css2?family=Oswald:wght@400;500;600;700&family=Roboto+Condensed:wght@300;400;700&display=swap" rel="stylesheet">
<style>
  :root {
    --page: #ffffff;
    --poster-bg: #262626;
    --poster-bg-deep: #1b1b1b;
    --gold: #f6c51a;
    --blue-top: #27a6ea;
    --blue-bottom: #0d63ae;
    --olive: #6b8b22;
    --lime: #b6d63a;
    --white: #ffffff;
    --muted: #d6d6d6;
    --photo-light: #8a7060;
    --photo-dark: #2e2926;
  }
  * { margin: 0; padding: 0; box-sizing: border-box; }
  html, body {
    width: 1200px; height: 960px; overflow: hidden;
    background: var(--page);
  }
  .poster {
    position: absolute; left: 300px; top: 31px;
    width: 600px; height: 900px; overflow: hidden;
    background: linear-gradient(160deg, var(--poster-bg) 0%, var(--poster-bg-deep) 100%);
    font-family: "Roboto Condensed", "Arial Narrow", sans-serif;
    color: var(--white);
  }
  .hero-photo {
    position: absolute; left: 214px; top: 0; width: 386px; height: 440px;
    background: radial-gradient(ellipse at 55% 45%, var(--photo-light) 0%, var(--photo-dark) 60%, var(--poster-bg) 100%);
  }
  .brand {
    position: absolute; left: 26px; top: 40px;
  }
  .brand-mark {
    width: 20px; height: 20px; border: 3px solid var(--white); margin-bottom: 14px;
  }
  .brand-name {
    font-family: "Oswald", sans-serif; font-weight: 600;
    font-size: 30px; line-height: 1; letter-spacing: 1px; text-transform: uppercase;
  }
  .brand-by {
    font-family: "Oswald", sans-serif; font-weight: 600;
    font-size: 30px; line-height: 1.2; text-transform: uppercase; letter-spacing: 1px;
  }
  .offer {
    position: absolute; left: 26px; top: 222px;
    font-family: "Oswald", sans-serif; font-weight: 700;
    font-size: 48px; line-height: 60px; color: var(--gold);
  }
  .event-band {
    position: absolute; left: 0; top: 440px; width: 600px; height: 120px;
    background: linear-gradient(180deg, var(--blue-top) 0%, var(--blue-bottom) 100%);
    text-align: center; padding-top: 14px;
    font-family: "Oswald", sans-serif; text-transform: uppercase;
  }
  .event-venue { font-size: 44px; font-weight: 600; line-height: 52px; }
  .event-title { font-size: 33px; font-weight: 500; line-height: 40px; }
  .classes-band {
    position: absolute; left: 0; top: 566px; width: 600px; height: 34px;
    background: var(--olive);
    font-family: "Oswald", sans-serif; font-weight: 500; text-transform: uppercase;
    font-size: 20px; line-height: 34px; text-align: center;
  }
  .schedule {
    position: absolute; right: 17px; top: 622px; width: 566px; text-align: right;
  }
  .schedule-title {
    font-family: "Oswald", sans-serif; font-weight: 500; text-transform: uppercase;
    font-size: 34px; line-height: 44px; color: var(--gold);
  }
  .schedule-list { list-style: none; }
  .schedule-item { font-size: 20px; line-height: 30px; color: var(--muted); }
  .schedule-item b { color: var(--white); font-weight: 700; }
  .schedule-item b::before { content: "•"; margin-right: 2px; }
  .event-dates {
    position: absolute; left: 17px; right: 17px; top: 818px;
    font-size: 23px; font-weight: 300; color: var(--muted); white-space: nowrap; text-align: right;
  }
  .contact {
    position: absolute; left: 0; right: 0; top: 864px; text-align: center;
    font-size: 15px; color: var(--lime);
  }
</style>
</head>
<body>
  <main class="poster">
    <div class="hero-photo" role="img" aria-label="Photograph of a fit trainer in black sportswear throwing a punch toward the viewer"></div>

    <header class="brand">
      <div class="brand-mark"></div>
      <div class="brand-name">Vita Forge</div>
      <div class="brand-by" style="font-size:16px;font-weight:400;">by Dale Wintham</div>
    </header>

    <h2 class="offer">PLUS: 30 Minute<br>Private Training<br>Sessions</h2>

    <section class="event-band">
      <h1 class="event-venue">The Halcott Spires Gym</h1>
      <p class="event-title">Complimentary Fitness &amp; Wellness</p>
    </section>

    <p class="classes-band">Complimentary Yoga, Pilates &amp; Interval Training Bootcamp Classes</p>

    <section class="schedule">
      <h3 class="schedule-title">Schedule:</h3>
      <ul class="schedule-list">
        <li class="schedule-item"><b>Halcott Spires Gym</b> 9:00am - 9:30am</li>
        <li class="schedule-item"><b>Yoga</b> 9:45am - 10:15am</li>
        <li class="schedule-item"><b>Interval Training Bootcamp</b> 11:45am -12:15pm</li>
        <li class="schedule-item"><b>Pilates</b> 9:00am - 12:00pm</li>
        <li class="schedule-item"><b>Kids Karate Classes Also Available</b></li>
      </ul>
    </section>

    <p class="event-dates">Saturday May 18th, 25th &amp; June 1st Time: 9:00am - 12:15pm</p>

    <p class="contact">www.Vitaforge.tv Info@vitaforge.tv</p>
  </main>
</body>
</html>
```